BrightLedgerMoney(.com) needs website & logo design

We need our website mock-up made into a reality! We are wanting to launch a multifaceted website for all things financial - i.e. blogs, financial wellness information, and a network of redirect links.
We have an existing mock-up, which I will include, but are open to your creative approach!

Industry/Entity Type

Finance

Coding

Coded - Design and coding required

Number of Pages Required

1 page

Requirements
Must have
• Corresponding logo

```html
<!DOCTYPE html>
<html lang="en">
<head>
<meta charset="utf-8">
<title>Bright Ledger Money</title>
<link rel="stylesheet" href="https://fonts.googleapis.com/css2?family=Montserrat:wght@400;500;600;700&family=Nunito+Sans:wght@700;800;900&family=Playfair+Display:wght@700&display=swap">
<style>
:root{
  --teal:#72d9c1;
  --ink:#1f2529;
  --text:#4a4f54;
  --muted:#7b8186;
  --soft:#f4f2f2;
  --line:#e7e7e7;
  --night:#262d33;
  --foot:#1c1e21;
  --white:#ffffff;
}
*{margin:0;padding:0;box-sizing:border-box}
html,body{width:1200px;height:3572px;overflow:hidden}
body{position:relative;background:var(--white);font-family:"Montserrat",sans-serif;color:var(--ink)}
.heading{font-family:"Nunito Sans",sans-serif;font-weight:800;text-transform:uppercase}
.btn{position:absolute;display:flex;align-items:center;justify-content:center;background:var(--teal);color:var(--ink);font-family:"Nunito Sans",sans-serif;font-weight:900;font-size:14px;text-transform:uppercase;text-decoration:none}
.rule{position:absolute;height:3px;background:var(--teal)}
.logo{font-family:"Playfair Display",serif;font-weight:700;font-size:24px;color:var(--ink);white-space:nowrap}

/* header */
.site-header{position:absolute;left:0;top:0;width:1200px;height:93px;background:var(--white)}
.site-header .logo{position:absolute;left:133px;top:30px}
.nav{position:absolute;top:35px;font-size:12.5px;font-weight:500;color:var(--ink);text-transform:uppercase;white-space:nowrap}
.nav.active{color:var(--teal);border-top:2px solid var(--teal);border-bottom:2px solid var(--teal);padding:3px 0;top:30px}

/* hero */
.hero{position:absolute;left:0;top:93px;width:1200px;height:607px;background:linear-gradient(90deg,#2c3a48 0%,#4f6272 30%,#6a7a84 48%,#5d6c76 60%,#3c4b58 100%)}
.hero-glow{position:absolute;left:480px;top:0;width:260px;height:420px;background:radial-gradient(ellipse at 50% 35%,rgba(255,184,104,.75),rgba(255,184,104,0) 70%)}
.hero h1{position:absolute;left:133px;top:183px;font-family:"Nunito Sans",sans-serif;font-weight:900;font-size:40px;line-height:45px;color:var(--white);text-transform:uppercase;white-space:nowrap}
.hero p{position:absolute;left:133px;top:330px;width:300px;font-size:19.5px;line-height:28px;color:var(--white)}

/* signup */
.signup{position:absolute;left:0;top:700px;width:1200px;height:121px;background:var(--soft)}
.signup h2{position:absolute;left:133px;top:42px;font-size:23px;color:var(--ink);white-space:nowrap}
.email-field{position:absolute;left:400px;top:37px;width:467px;height:51px;background:var(--white);border:1px solid #c9c9c9;display:flex;align-items:center;padding-left:20px;gap:16px;font-size:14px;color:var(--muted)}

/* topics grid */
.topics{position:absolute;left:0;top:821px;width:1200px;height:425px}
.topic{position:absolute;height:212px;border-right:1px solid var(--line);border-bottom:1px solid var(--line);text-align:center}
.topic .art{width:52px;height:52px;margin:60px auto 0;border-radius:50%}
.topic span{display:block;margin-top:20px;font-size:16px;font-weight:500}

/* welcome */
.welcome{position:absolute;left:0;top:1246px;width:1200px;height:543px;background:var(--soft)}
.welcome-photo{position:absolute;left:440px;top:0;width:760px;height:543px;background:radial-gradient(ellipse at 58% 50%,#b9c3cc 0%,#d9dde1 35%,rgba(244,242,242,0) 70%)}
.welcome .kicker{position:absolute;left:134px;top:48px;font-size:23px;color:var(--ink)}
.welcome .title{position:absolute;left:134px;top:82px;font-family:"Nunito Sans",sans-serif;font-weight:900;font-size:29px;color:var(--teal);text-transform:uppercase;white-space:nowrap}
.welcome p{position:absolute;left:133px;top:166px;width:355px;font-size:13.6px;line-height:20.8px;text-align:justify;color:var(--text)}

/* tools strip */
.tools{position:absolute;left:133px;top:1727px;width:935px;height:126px;background:var(--white);box-shadow:0 4px 16px rgba(0,0,0,.07);display:flex}
.tool{border-right:1px solid var(--line);text-align:center;font-size:14px;color:var(--text)}
.tool:last-child{border-right:none}
.tool .art{width:40px;height:40px;margin:26px auto 10px;border-radius:8px}

/* blog */
.section-title{position:absolute;left:0;width:1200px;text-align:center;font-size:24px;color:var(--ink)}
.card{position:absolute;top:1993px;width:296px;height:438px;background:var(--white);box-shadow:0 3px 14px rgba(0,0,0,.06)}
.card .photo{height:191px}
.card h3{margin:30px 29px 0;font-size:14px;line-height:21px;font-weight:700;color:var(--ink)}
.card p{margin:12px 29px 0;font-size:11.5px;line-height:17.5px;color:var(--muted)}
.card .btn{left:29px;top:377px;width:82px;height:30px;font-size:10px;color:var(--white)}
.bracket{position:absolute;width:32px;height:34px;border-color:#e2e2e2;border-style:solid}

/* wellness */
.wellness{position:absolute;left:0;top:2497px;width:1200px;height:459px;background:var(--night)}
.wellness-photo{position:absolute;left:0;top:0;width:620px;height:459px;background:radial-gradient(ellipse at 48% 55%,#5b6b76 0%,#39454e 40%,rgba(38,45,51,0) 75%)}
.wellness h2{position:absolute;left:655px;top:50px;font-size:24px;color:var(--white);white-space:nowrap}
.wellness p{position:absolute;left:656px;top:136px;width:409px;font-size:14.6px;line-height:22.5px;text-align:justify;color:#c9cdd0}

/* questions */
.questions{position:absolute;left:0;top:2956px;width:1200px;height:254px;background:var(--teal)}
.questions h2{position:absolute;left:0;top:46px;width:1200px;text-align:center;font-size:24px;color:#2b3338}
.questions p{position:absolute;left:200px;top:94px;width:800px;text-align:center;font-size:14px;line-height:22.5px;color:#3d4a4f}
.questions .btn{left:532px;top:166px;width:136px;height:44px;background:var(--white)}

/* footer */
.site-footer{position:absolute;left:0;top:3210px;width:1200px;height:362px;background:var(--foot);color:var(--white)}
.site-footer .logo{position:absolute;left:136px;top:130px;color:var(--white)}
.foot-head{position:absolute;top:46px;font-size:13px;font-weight:700;text-transform:uppercase}
.foot-rule{position:absolute;top:79px;height:2px;background:var(--white)}
.contact-item{position:absolute;left:416px;display:flex;align-items:center;gap:10px;font-size:11.5px;line-height:16px;white-space:nowrap}
.contact-item .dot{width:22px;height:22px;border-radius:50%;background:var(--white);flex:none;display:flex;align-items:center;justify-content:center}
.menu-links{position:absolute;left:680px;top:101px;list-style:none;font-size:11.5px;line-height:22.5px}
.social{position:absolute;top:109px;width:34px;height:34px;border-radius:50%;background:var(--teal)}
.foot-divider{position:absolute;left:133px;top:280px;width:935px;height:1px;background:#3a3d41}
.copyright{position:absolute;left:0;top:313px;width:1200px;text-align:center;font-size:11px}
</style>
</head>
<body>

<header class="site-header">
  <div class="logo">Bright Ledger Money</div>
  <a class="nav active" style="left:624px">Home</a>
  <a class="nav" style="left:698px">About Us</a>
  <a class="nav" style="left:804px">Services</a>
  <a class="nav" style="left:907px">Blog</a>
  <a class="nav" style="left:985px">Contact Us</a>
</header>

<section class="hero" role="img" aria-label="Businessman climbing a staircase toward a sunlit city skyline with rising arrows">
  <div class="hero-glow"></div>
  <h1>A Clear Path<br>to Financial<br>Wellness</h1>
  <p>Having insight to relevant information is what we bring to you in a clear and easy to digest way.</p>
  <a class="btn" style="left:133px;top:476px;width:117px;height:43px">Read More</a>
</section>

<section class="signup">
  <h2 class="heading">Signup for Free</h2>
  <div class="rule" style="left:133px;top:84px;width:83px"></div>
  <div class="email-field">
    <svg width="18" height="13" viewBox="0 0 18 13"><rect x="0.75" y="0.75" width="16.5" height="11.5" fill="none" stroke="#333" stroke-width="1.5"/><path d="M1 1l8 6 8-6M1 12l6-5M17 12l-6-5" fill="none" stroke="#333" stroke-width="1.3"/></svg>
    <span>Yoru Email</span>
  </div>
  <a class="btn" style="left:886px;top:37px;width:182px;height:51px;font-size:15px">Get Started</a>
</section>

<section class="topics">
  <div class="topic" style="left:0;top:0;width:449px"><div class="art" role="img" aria-label="Target with arrow icon" style="background:radial-gradient(circle,#e74c3c 20%,#fff 21% 38%,#3a8ee6 39%)"></div><span>Set Goals</span></div>
  <div class="topic" style="left:449px;top:0;width:313px"><div class="art" role="img" aria-label="Banknote and coins icon" style="border-radius:10px;background:linear-gradient(135deg,#3fae5c,#f5b82e)"></div><span>Money 101</span></div>
  <div class="topic" style="left:762px;top:0;width:438px;border-right:none"><div class="art" role="img" aria-label="Calculator and coins icon" style="border-radius:8px;background:linear-gradient(135deg,#f3a93b,#3a4a5a)"></div><span>Budgeting</span></div>
  <div class="topic" style="left:0;top:212px;width:449px"><div class="art" role="img" aria-label="Mindfulness figure icon" style="background:linear-gradient(135deg,#7b4fbf,#f0b64a)"></div><span>Credit Mindfulness</span></div>
  <div class="topic" style="left:449px;top:212px;width:313px"><div class="art" role="img" aria-label="Debt chart icon" style="background:linear-gradient(135deg,#f7d04a,#e8508a)"></div><span>Debt Management</span></div>
  <div class="topic" style="left:762px;top:212px;width:438px;border-right:none"><div class="art" role="img" aria-label="Retiree with coin stacks icon" style="border-radius:8px;background:linear-gradient(135deg,#4a76c8,#f3a93b)"></div><span>Retirement Planning</span></div>
</section>

<section class="welcome">
  <div class="welcome-photo" role="img" aria-label="Hand with pen reviewing charts on a laptop beside a coffee cup"></div>
  <div class="kicker heading">Welcome to</div>
  <div class="title">Bright Ledger Money</div>
  <div class="rule" style="left:134px;top:129px;width:55px"></div>
  <p>There are many variations of passages of Lorem Ipsum available, but the majority have suffered alteration in some form, by injected humour, or randomised words which don't look even slightly believable. If you are going to use a passage of Lorem Ipsum, you need to be sure there isn't anything embarrassing hidden in the middle of text. All the Lorem Ipsum generators on the Internet tend to repeat predefined</p>
  <a class="btn" style="left:133px;top:384px;width:117px;height:43px">Read More</a>
</section>

<div class="tools">
  <div class="tool" style="width:147px"><div class="art" role="img" aria-label="Money bag icon" style="background:linear-gradient(135deg,#f5b82e,#e78b2b)"></div>Save</div>
  <div class="tool" style="width:150px"><div class="art" role="img" aria-label="Budget icon" style="background:linear-gradient(135deg,#f3a93b,#3fae5c)"></div>Budget</div>
  <div class="tool" style="width:165px"><div class="art" role="img" aria-label="Calculator icon" style="background:linear-gradient(135deg,#e74c3c,#333)"></div>Calculate</div>
  <div class="tool" style="width:158px"><div class="art" role="img" aria-label="Rising bar chart icon" style="background:linear-gradient(135deg,#e74c3c,#f5b82e)"></div>Track</div>
  <div class="tool" style="width:168px"><div class="art" role="img" aria-label="Research icon" style="background:linear-gradient(135deg,#3a8ee6,#f5b82e)"></div>Research</div>
  <div class="tool" style="width:147px"><div class="art" role="img" aria-label="Invest icon" style="background:linear-gradient(135deg,#3fae5c,#f5b82e)"></div>Invest</div>
</div>

<h2 class="section-title heading" style="top:1902px;font-weight:700">Latest Blog</h2>
<div class="rule" style="left:579px;top:1950px;width:42px"></div>

<div class="bracket" style="left:125px;top:2408px;border-width:0 0 8px 8px"></div>
<div class="bracket" style="left:1045px;top:1985px;border-width:8px 8px 0 0"></div>

<article class="card" style="left:133px">
  <div class="photo" role="img" aria-label="Businessman touching a glowing financial chart" style="background:linear-gradient(135deg,#1d4e74,#3c8fb5 60%,#0f2f48)"></div>
  <h3>Lorem Ipsum is simply dummy text of the printing</h3>
  <p>There are many variations of passages of Lorem Ipsum available, but the majority have suffered alteration in some form, by injected humour, or randomised</p>
  <a class="btn">Read More</a>
</article>
<article class="card" style="left:453px">
  <div class="photo" role="img" aria-label="Team reviewing charts on a desk with a laptop" style="background:linear-gradient(135deg,#1f3a57,#8aa6bf 55%,#d8dde2)"></div>
  <h3>Lorem Ipsum is simply dummy text of the printing</h3>
  <p>There are many variations of passages of Lorem Ipsum available, but the majority have suffered alteration in some form, by injected humour, or randomised</p>
  <a class="btn">Read More</a>
</article>
<article class="card" style="left:773px">
  <div class="photo" role="img" aria-label="Man viewing a transparent financial report display" style="background:linear-gradient(135deg,#cfdbe6,#8eb0cc 50%,#e4ebf1)"></div>
  <h3>Lorem Ipsum is simply dummy text of the printing</h3>
  <p>There are many variations of passages of Lorem Ipsum available, but the majority have suffered alteration in some form, by injected humour, or randomised</p>
  <a class="btn">Read More</a>
</article>

<section class="wellness">
  <div class="wellness-photo" role="img" aria-label="Open hand holding coin stacks with a rising glowing chart arrow"></div>
  <h2 class="heading">Financial Wellness</h2>
  <div class="rule" style="left:656px;top:90px;width:42px"></div>
  <p>There are many variations of passages of Lorem Ipsum available, but the majority have suffered alteration in some form, by injected humour, or randomised words which don't look even slightly believable. If you are going to use a passage of Lorem Ipsum, you need to be sure there isn't anything embarrassing hidden in the middle of text. All the Lorem Ipsum generators on the Internet tend to repeat predefined as necessary, making this the first true generator on the Internet.</p>
  <a class="btn" style="left:656px;top:365px;width:118px;height:43px">Read More</a>
</section>

<section class="questions">
  <h2 class="heading">Have Any Questions?</h2>
  <p>There are many variations of passages of Lorem Ipsum available, but the majority have suffered alteration in some form, by injected humour, or randomised words which don't look even slightly believable.</p>
  <a class="btn">Contact Us</a>
</section>

<footer class="site-footer">
  <div class="logo">Bright Ledger Money</div>

  <div class="foot-head" style="left:416px">Contact Us</div>
  <div class="foot-rule" style="left:416px;width:193px"></div>
  <div class="contact-item" style="top:105px">
    <span class="dot"><svg width="10" height="12" viewBox="0 0 10 12"><path d="M5 0a4 4 0 0 0-4 4c0 3 4 8 4 8s4-5 4-8a4 4 0 0 0-4-4z" fill="#1c1e21"/><circle cx="5" cy="4" r="1.4" fill="#fff"/></svg></span>Harbor Point, OR
  </div>
  <div class="contact-item" style="top:150px">
    <span class="dot"><svg width="11" height="11" viewBox="0 0 11 11"><path d="M2 0.5l2 2.3-1 1.3a6 6 0 0 0 3.9 3.9l1.3-1 2.3 2-1 1.8C5 10.6 0.4 6 0.2 1.5z" fill="#1c1e21"/></svg></span><span>Call Us<br>+1 555 010 0199</span>
  </div>
  <div class="contact-item" style="top:203px">
    <span class="dot"><svg width="11" height="8" viewBox="0 0 11 8"><rect width="11" height="8" rx="1" fill="#1c1e21"/><path d="M0.5 0.8l5 3.6 5-3.6" fill="none" stroke="#fff" stroke-width="1"/></svg></span><span>E mail Us<br>info@brightledgermoney.com</span>
  </div>

  <div class="foot-head" style="left:678px">Menu</div>
  <div class="foot-rule" style="left:678px;width:107px"></div>
  <ul class="menu-links">
    <li>Home</li><li>About Us</li><li>Services</li><li>Blog</li><li>Contact Us</li>
  </ul>

  <div class="foot-head" style="left:836px">Follow</div>
  <div class="foot-rule" style="left:836px;width:107px"></div>
  <a class="social" style="left:833px" aria-label="Social profile"></a>
  <a class="social" style="left:876px" aria-label="Social profile"></a>
  <a class="social" style="left:919px" aria-label="Social profile"></a>
  <a class="social" style="left:968px" aria-label="Social profile"></a>
  <a class="social" style="left:1017px" aria-label="Social profile"></a>

  <div class="foot-divider"></div>
  <div class="copyright">Copyright © 2023 All Rights Reserved</div>
</footer>

</body>
</html>
```